Business Card and Letterhead for Pimlu - modern real estate business

I need a double sided business card design for Pimlu. Please see business card brief here https://files.trelvonadocs.com/sheet/r/7QzTmWbaXLJnoPEd-kRyUgFhHsstbvCe2qfoMxDa_pz/view?mode=shared

Please feel free to design the business cards however you feel best. I am happy to give some creative freedoms and then provide feedback from there.

Please then also create a letterhead to match the business card design

Colors

Designer to choose colors to be used in the design.

Requirements
Must have
• Must be a modern, elegant business card which looks very professional

```html
<!DOCTYPE html>
<html lang="en">
<head>
<meta charset="utf-8">
<title>Pimlu Business Card</title>
<link rel="stylesheet" href="https://fonts.googleapis.com/css2?family=EB+Garamond:wght@400;600&display=swap">
<style>
  :root {
    --ink: #000000;
    --red: #e3101e;
    --white: #f4f4f4;
    --page: #1c1c1c;
    --photo-sky: #c9d6dc;
    --photo-green: #6f8a4a;
    --photo-dark: #3a4a2e;
  }
  * { box-sizing: border-box; margin: 0; padding: 0; }
  html, body { width: 1200px; height: 900px; overflow: hidden; }
  body {
    background: var(--page);
    font-family: "EB Garamond", Georgia, serif;
    position: relative;
  }
  .card {
    position: absolute;
    left: 300px;
    width: 600px;
    height: 343px;
    background: var(--ink);
    box-shadow: 0 14px 30px rgba(0,0,0,.55);
    overflow: hidden;
  }
  .card-front {
    top: 80px;
    border: 2px solid var(--red);
    display: flex;
    align-items: center;
    justify-content: center;
  }
  .brand-name {
    color: var(--red);
    font-weight: 600;
    font-size: 112px;
    letter-spacing: 10px;
    line-height: 1;
    text-transform: uppercase;
  }
  .card-back { top: 477px; display: flex; }
  .details {
    width: 300px;
    padding: 58px 0 0 40px;
    position: relative;
  }
  .agent-name {
    color: var(--red);
    font-weight: 600;
    font-size: 25px;
    letter-spacing: .5px;
    text-transform: uppercase;
    line-height: 1;
  }
  .agent-role {
    color: var(--white);
    font-size: 15px;
    text-transform: uppercase;
    margin-top: 4px;
  }
  .agent-web {
    color: var(--red);
    font-size: 13px;
    letter-spacing: 3px;
    margin-top: 4px;
  }
  .contact-list {
    list-style: none;
    position: absolute;
    left: 40px;
    bottom: 34px;
  }
  .contact-list li {
    display: flex;
    align-items: center;
    gap: 10px;
    color: var(--white);
    font-size: 16px;
    line-height: 1.45;
  }
  .contact-list svg { width: 14px; height: 14px; fill: var(--red); flex: none; }
  .contact-address {
    color: var(--red);
    font-weight: 600;
    font-size: 16px;
    line-height: 1.2;
    margin-top: 3px;
  }
  .divider { width: 3px; background: var(--red); }
  .portrait {
    flex: 1;
    background: linear-gradient(160deg, var(--photo-sky) 0%, var(--photo-green) 45%, var(--photo-dark) 100%);
  }
</style>
</head>
<body>
  <section class="card card-front">
    <span class="brand-name">Pimlu</span>
  </section>

  <section class="card card-back">
    <div class="details">
      <h1 class="agent-name">Liam Hartley</h1>
      <p class="agent-role">Licenced Real Estate Agent</p>
      <p class="agent-web">www.pimlu.com</p>

      <ul class="contact-list">
        <li>
          <svg viewBox="0 0 14 14" aria-hidden="true"><path d="M4 1h6a1 1 0 0 1 1 1v10a1 1 0 0 1-1 1H4a1 1 0 0 1-1-1V2a1 1 0 0 1 1-1zm0 1.5v8.5h6V2.5z"/></svg>
          0412 555 018
        </li>
        <li>
          <svg viewBox="0 0 14 14" aria-hidden="true"><path d="M1 5c0-2 3-3 6-3s6 1 6 3v1h-3V4.5H4V6H1zm2 2h8l1 5H2z"/></svg>
          1300 555 274
        </li>
        <li>
          <svg viewBox="0 0 14 14" aria-hidden="true"><path d="M1 3h12v8H1zm1 1v.4l5 3.4 5-3.4V4z"/></svg>
          liam@pimlu.com
        </li>
        <li class="contact-address">PO Box 1187,<br>Ashford NSW 2361</li>
      </ul>
    </div>
    <div class="divider"></div>
    <div class="portrait" role="img" aria-label="Portrait photo of the agent in a dark suit, outdoors with trees and a valley behind"></div>
  </section>
</body>
</html>
```